Redesign Canvas Art E-Commerce Website

Help! I hired a couple of companies on Brisklo.com to build and design an e-commerce website for me. After three long and painful months, I have one that I believe is functional on the back-end, but aesthetically on the front end is a mess.

We are a small family business that will take your digital photo and manipulate it into a digitally created oil, watercolor or impressionist style pieces of artwork that we print on museum quality, gallery grade canvas and ship to the customer, ready to hang.

We are looking to create an e-commerce website where a customer can choose their art style, upload a photo, choose their canvas size and orientation (horizontal or vertical) and checkout. Within 48 hours, we will send them back a proof of their newly created, customized artwork for them to approve or not approve. If they approve, we print, package and ship them the product. If they do not approve, we offer unlimited revisions until they are happy.

As I mentioned, the back end functionality is already there, just need design help. No coding required

Here is a link to the development page that they created: https://plumwickstudio.com/development/

As you can see, it looks off...doesnt line up properly, wasted space, weird font. Feel free to either correct the homepage they created or design an entirely new page. I am attaching some examples of before and after photos of artwork for reference. I also think the testimonials page and shop page can use a little style. The content is there and accurate, it just doesn't look pretty. Please keep in mind that our customers will probably not be very tech savvy. The customers will probably be sending us pics of kids, grandkids, pets, family portraits, vacation photos, etc.

Here is one of our competitors - www.gildavantry.com
Their website looks clean and inviting.

Thank you in advance! Im looking forward to seeing the results. I am including our logo in the attachments (I do not have it in a vector file, just a jpeg)

Target Market(s)

Non tech-savvy indiduals, 30-70 years old

Industry/Entity Type

Please look at https://plumwickstudio.com/development/ to see various pages and what the other designers did

Number of Pages Required

1 page

Requirements
Must have
• Verbiage on pages leave "as is" but feel free to change styles. Would like to keep existing four categories on homepage
Nice to have
• Warm and inviting homepage that evokes emotion

```html
<!DOCTYPE html>
<html lang="en">
<head>
<meta charset="utf-8">
<title>Brushvale Prints – Turn Your Digital Photos Into Wall Art</title>
<link href="https://fonts.googleapis.com/css2?family=Lobster&family=Mulish:wght@400;600;700&display=swap" rel="stylesheet">
<style>
:root{
  --yellow:#f8d432;
  --orange:#ef7d1e;
  --blue:#2bb0d0;
  --dark:#2b2b2b;
  --ink:#222;
  --muted:#555;
  --white:#fff;
  --frame:#c9c9c9;
  --footer-text:#e2e2e2;
}
*{box-sizing:border-box;margin:0;padding:0}
html,body{width:1200px;height:4270px;overflow:hidden}
body{position:relative;font-family:"Mulish",sans-serif;color:var(--ink);background:var(--white)}
.abs{position:absolute}
.script{font-family:"Lobster",cursive;font-weight:400}

/* header */
.site-header{left:0;top:0;width:1200px;height:88px;background:var(--white)}
.brand{left:113px;top:22px;display:flex;align-items:center;gap:10px;font-size:24px;font-weight:700;color:var(--ink)}
.brand-dot{width:36px;height:36px;border-radius:50%;background:var(--orange)}
.main-nav{left:469px;top:32px;display:flex;gap:22px;font-size:14px;color:#333}
.main-nav .active{color:var(--orange)}
.cart{left:1052px;top:28px}
.cart-count{left:1071px;top:23px;width:16px;height:16px;border-radius:50%;background:var(--orange);color:#fff;font-size:10px;text-align:center;line-height:16px}

/* hero */
.hero{left:0;top:88px;width:1200px;height:780px;background:linear-gradient(100deg,#7a4a35 0%,#3f5a2c 25%,#2f4a22 50%,#6b5e4a 75%,#9a9488 100%)}
.hero-title{left:111px;top:322px;width:480px;font-size:50px;line-height:60px;color:var(--white);white-space:nowrap}
.scroll-down{left:553px;top:818px;width:92px;height:92px;border-radius:50%;background:var(--white)}

/* categories */
.section-title{width:1200px;left:0;text-align:center;font-size:40px}
.cat{top:1036px;width:229px}
.cat-img{width:229px;height:170px;border:4px solid var(--frame)}
.cat-name{margin-top:16px;text-align:center;font-size:21px;font-weight:600}
.btn{display:block;margin:10px auto 0;width:144px;height:38px;border-radius:19px;background:linear-gradient(90deg,var(--yellow),var(--orange));color:#fff;font-size:12px;font-weight:700;text-align:center;line-height:38px}

/* best sellers */
.band-yellow{left:0;top:1403px;width:1200px;height:663px;background:var(--yellow)}
.product{top:1569px;width:305px;height:386px;background:var(--white);border-radius:4px;box-shadow:0 6px 18px rgba(0,0,0,.12)}
.product-img{position:absolute;left:25px;top:18px;width:256px;height:200px;border-radius:24px}
.product-name{position:absolute;left:38px;top:254px;font-size:17px}
.rating{position:absolute;left:38px;top:287px;display:flex;align-items:center;gap:4px;font-size:16px}
.price{position:absolute;left:38px;top:322px;font-size:26px;font-weight:600}
.arrow{top:1745px;width:34px;height:34px;border-radius:50%;background:var(--white)}

/* about */
.orange-block{left:600px;top:2066px;width:600px;height:580px;background:var(--orange)}
.laptop{left:217px;top:2129px;width:769px;height:505px;background:#e6e6e6;border-radius:16px 16px 0 0}
.laptop-screen{left:252px;top:2164px;width:697px;height:433px;background:linear-gradient(120deg,#f4e8e2,#e9c9b6 45%,#fbf6f2)}
.laptop-base{left:129px;top:2634px;width:945px;height:26px;background:linear-gradient(#eee,#d6d6d6);border-radius:0 0 40% 40%/0 0 100% 100%;box-shadow:0 18px 30px rgba(0,0,0,.1)}
.about-copy{left:196px;top:2812px;width:808px;font-size:14px;line-height:21.5px;color:var(--muted);text-align:justify;text-align-last:center}
.about-copy p{margin-bottom:21px}

/* why us */
.band-blue{left:0;top:3201px;width:1200px;height:593px;background:var(--blue)}
.why{top:3374px;width:345px;height:345px;border-radius:50%;background:var(--white);display:flex;align-items:center;justify-content:center}
.why-inner{width:315px;height:315px;border-radius:50%;display:flex;flex-direction:column;align-items:center;justify-content:center;text-align:center;padding:0 45px}
.why-inner h3{font-size:18px;font-weight:600;margin:14px 0 14px}
.why-inner p{font-size:11px;line-height:20px}
.y{background:var(--yellow);color:var(--ink)}
.o{background:var(--orange);color:var(--white)}

/* footer */
.site-footer{left:0;top:3794px;width:1200px;height:476px;background:var(--dark)}
.f-head{top:3893px;font-size:21px;font-weight:600;color:var(--white)}
.f-links{left:111px;top:3944px;list-style:none;font-size:13px;line-height:25.7px;color:var(--footer-text)}
.f-text{font-size:13px;line-height:25px;color:var(--footer-text)}
.newsletter{left:411px;top:4056px;width:343px;height:36px;border-radius:18px;background:#fff;border:2px solid #ccc}
.newsletter span{position:absolute;left:20px;top:9px;font-size:11px;color:#777}
.newsletter b{position:absolute;right:4px;top:3px;width:84px;height:26px;border-radius:13px;background:var(--orange);color:#fff;font-size:11px;text-align:center;line-height:26px}
.copyright{left:0;top:4164px;width:1200px;text-align:center;font-size:13px;color:#fff}
.social{top:4200px;width:25px;height:25px;border-radius:50%;background:#fff}
</style>
</head>
<body>

<header class="site-header abs">
  <div class="brand abs"><span class="brand-dot"></span>Brushvale Prints</div>
  <nav class="main-nav abs">
    <span class="active">Home</span><span>Shop</span><span>Testimonials</span><span>About Us</span><span>FAQs</span><span>My Orders</span><span>Contact Us</span>
  </nav>
  <svg class="cart abs" width="26" height="24" viewBox="0 0 26 24" fill="none" stroke="#555" stroke-width="1.6"><path d="M1 2h4l3 13h13l3-9H7"/><circle cx="10" cy="20" r="2"/><circle cx="19" cy="20" r="2"/></svg>
  <div class="cart-count abs">0</div>
</header>

<section class="hero abs" role="img" aria-label="Painted canvas of a bride and groom embracing in front of greenery, leaning against a brick wall beside a phone showing the original photo"></section>
<h1 class="hero-title abs script">Turn Your Digital<br>Photos Into One of<br>a Kind Wall Art</h1>
<div class="scroll-down abs">
  <svg width="92" height="92" viewBox="0 0 92 92">
    <defs><path id="arc" d="M18 50a28 28 0 0 1 56 0"/></defs>
    <text font-size="9" letter-spacing="2" fill="#333" font-family="Mulish, sans-serif"><textPath href="#arc">SCROLL DOWN</textPath></text>
    <path d="M40 46l6 5 6-5M40 52l6 5 6-5" stroke="#333" stroke-width="1.5" fill="none"/>
  </svg>
</div>

<h2 class="section-title abs script" style="top:962px;">Categories</h2>
<div class="cat abs" style="left:111px"><div class="cat-img" role="img" aria-label="Oil painting style portrait of a couple" style="background:linear-gradient(135deg,#3c5a2a,#a07a5a,#f0e8e0)"></div><div class="cat-name">Oil</div><span class="btn">GET STARTED</span></div>
<div class="cat abs" style="left:361px"><div class="cat-img" role="img" aria-label="Watercolor style image of a mother and baby" style="background:linear-gradient(135deg,#fbf3ee,#eec7b0,#fff)"></div><div class="cat-name">Watercolor</div><span class="btn">GET STARTED</span></div>
<div class="cat abs" style="left:610px"><div class="cat-img" role="img" aria-label="Impressionist style canal scene with a gondola" style="background:linear-gradient(180deg,#9a8a8a,#c24040 45%,#3fae90)"></div><div class="cat-name">Impressionist</div><span class="btn">GET STARTED</span></div>
<div class="cat abs" style="left:858px"><div class="cat-img" role="img" aria-label="Digital photo of two children eating ice cream" style="background:linear-gradient(135deg,#e9e6e0,#e3b58f,#5aaed0)"></div><div class="cat-name">Digital Photo</div><span class="btn">GET STARTED</span></div>

<section class="band-yellow abs"></section>
<h2 class="section-title abs script" style="top:1494px;color:#fff">Best Sellers</h2>
<div class="arrow abs" style="left:39px"><svg width="34" height="34"><path d="M19 12l-5 5 5 5" stroke="#333" stroke-width="1.6" fill="none"/></svg></div>
<div class="arrow abs" style="left:1127px"><svg width="34" height="34"><path d="M15 12l5 5-5 5" stroke="#333" stroke-width="1.6" fill="none"/></svg></div>
<article class="product abs" style="left:111px"><div class="product-img" role="img" aria-label="Painted portrait of a laughing older couple" style="background:linear-gradient(135deg,#cfe0d0,#d8c4b0,#9fc3e0)"></div><div class="product-name">Duis aute irure</div><div class="rating"><svg width="96" height="16" fill="none" stroke="var(--orange)"><g id="st"><path d="M8 1.5l2 4.3 4.6.5-3.4 3.1 1 4.6L8 11.6l-4.2 2.4 1-4.6L1.4 6.3 6 5.8z"/></g><use href="#st" x="20"/><use href="#st" x="40"/><use href="#st" x="60"/><use href="#st" x="80"/></svg>&nbsp;(66)</div><div class="price">$25.00</div></article>
<article class="product abs" style="left:447px"><div class="product-img" role="img" aria-label="Painted portrait of a smiling bride holding a bouquet" style="background:linear-gradient(135deg,#3a2418,#c88e6a,#e8e2c8)"></div><div class="product-name">Duis aute irure</div><div class="rating"><svg width="96" height="16" fill="none" stroke="var(--orange)"><use href="#st"/><use href="#st" x="20"/><use href="#st" x="40"/><use href="#st" x="60"/><use href="#st" x="80"/></svg>&nbsp;(66)</div><div class="price">$25.00</div></article>
<article class="product abs" style="left:784px"><div class="product-img" role="img" aria-label="Painted image of a rider jumping a horse" style="background:linear-gradient(135deg,#5a8fc8,#8a4a22,#c9dcef)"></div><div class="product-name">Duis aute irure</div><div class="rating"><svg width="96" height="16" fill="none" stroke="var(--orange)"><use href="#st"/><use href="#st" x="20"/><use href="#st" x="40"/><use href="#st" x="60"/><use href="#st" x="80"/></svg>&nbsp;(66)</div><div class="price">$25.00</div></article>

<div class="orange-block abs"></div>
<div class="laptop abs"></div>
<div class="laptop-screen abs" role="img" aria-label="Watercolor artwork of a mother kissing her baby"></div>
<div class="laptop-base abs"></div>

<h2 class="section-title abs script" style="top:2748px;">About Us</h2>
<div class="about-copy abs">
  <p>At Brushvale Prints, we take your digital photo and turn it into a one-of-a-kind piece of artwork!</p>
  <p>The process couldn't be any easier. Simply upload your photo, choose your art style and size, and let our team of skilled digital artists do the rest. Do you want to put your digital photo on canvas without an art style? No problem! Just choose the “Digital Photo/Retouching” category and upload your photo. We can print your photo “as is” or do some minor retouching (e.g. remove objects, enhance colors, lighten photo, etc)</p>
  <p>You will receive a proof in your email to approve within 1-2 days. Once approved, your customized artwork will be transferred to canvas and shipped from our design studio in Florida. Brushvale Prints art makes a great gift for just about any special occasion. Know someone with an upcoming birthday, anniversary, housewarming party, wedding or other event? We've got you covered!</p>
  <p>Turn your cherished memories into a customized canvas masterpiece today!</p>
</div>

<section class="band-blue abs"></section>
<h2 class="section-title abs script" style="top:3293px;color:#fff">Why us?</h2>
<div class="why abs" style="left:100px"><div class="why-inner y">
  <svg width="72" height="72" viewBox="0 0 72 72" fill="none" stroke="#222" stroke-width="2"><circle cx="36" cy="12" r="5"/><path d="M36 17l14 28-14 14-14-14z"/><path d="M36 40v19M10 30c10-14 42-14 52 0"/></svg>
  <h3>Your Idea Your Design</h3><p>Each art piece is customized for you! You choose your size, orientation and art style. Makes a perfect gift!!</p></div></div>
<div class="why abs" style="left:428px"><div class="why-inner o">
  <svg width="96" height="64" viewBox="0 0 96 64" fill="none" stroke="#fff" stroke-width="2"><circle cx="30" cy="22" r="16"/><path d="M30 22l7-7"/><path d="M50 22h18l12 14v14H44M46 50h-6"/><circle cx="56" cy="52" r="5"/><circle cx="80" cy="52" r="5"/><path d="M4 40h24M8 46h20"/></svg>
  <h3>Fast Shipping</h3><p>Your artwork is printed and shipped in the USA! We offer fast turnaround with transit times typically 3-7 days. Free tracking with each order!!</p></div></div>
<div class="why abs" style="left:755px"><div class="why-inner y">
  <svg width="64" height="72" viewBox="0 0 64 72" fill="none" stroke="#222" stroke-width="2"><circle cx="32" cy="28" r="22"/><circle cx="32" cy="28" r="14"/><path d="M32 20l3 6 6 1-4 4 1 6-6-3-6 3 1-6-4-4 6-1z"/><path d="M20 46l-6 22 10-6 6 8M44 46l6 22-10-6-6 8"/></svg>
  <h3>High Quality</h3><p>We've put a lot of effort ensuring your artwork is of the highest quality. Each piece is printed on the highest quality, gallery grade canvas. It is ready to hang upon arrival.!</p></div></div>

<footer class="site-footer abs"></footer>
<h4 class="f-head abs" style="left:111px">More Information</h4>
<ul class="f-links abs"><li>About Us</li><li>My Orders</li><li>Testimonials</li><li>Get Started</li><li>FAQs</li><li>Privacy Policy</li><li>Terms and Conditions</li></ul>
<h4 class="f-head abs" style="left:411px">Join Our Newsletter</h4>
<p class="f-text abs" style="left:411px;top:3944px;width:310px">Sign up for our e-mail and be the first who know our special offers! Be the first to receive exclusive content, product updates, promotions and much more.</p>
<div class="newsletter abs"><span>Email address</span><b>Submit</b></div>
<h4 class="f-head abs" style="left:822px">About</h4>
<p class="f-text abs" style="left:822px;top:3944px;width:267px;line-height:21.5px;text-align:justify">The process couldn't be any easier. Simply upload your photo, choose your art style and size, and let our team of skilled digital artists do the rest. Do you want to put your digital photo on canvas without an art style? No problem! Just choose the “Digital Photo /Retouching” category and upload your photo.</p>
<div class="copyright abs">Copyright © 2023 Company name | Privacy Policy | Terms &amp; Conditions</div>
<span class="social abs" style="left:558px"></span>
<span class="social abs" style="left:588px"></span>
<span class="social abs" style="left:618px"></span>

</body>
</html>
```